Request for Business Card Design

Hi. My name is Marlene, I am looking for a new business card design for my company, Quarrow Signal Instruments, LLC. I really like the design you did for Tarsel Venture and was hoping you could do something similar using our full logo and our mark. I am also open to any raised texture design using our mark. I have attached our full logo, which would need to be somewhere on the card, as well as the mark in both outline and full form, as well as our brand colors / guide. The card does not have to be white, as long as our logo and mark appear. I actually like darker colored business cards more, but am open to all options. If you are interested in working with me, please let me know. We would also take the business card design into letterhead design if you can do that.

```html
<!DOCTYPE html>
<html lang="en">
<head>
<meta charset="utf-8">
<title>Quarrow Signal Instruments – Business Card</title>
<link rel="stylesheet" href="https://fonts.googleapis.com/css2?family=Open+Sans:wght@400;600;700&display=swap">
<style>
  :root {
    --backdrop: #3a332f;
    --card: #151515;
    --card-edge: #1d1d1d;
    --accent: #1a9ccc;
    --ink: #f2f2f2;
    --ink-soft: #d8d8d8;
    --emboss: rgba(255, 255, 255, 0.035);
  }
  * { box-sizing: border-box; margin: 0; padding: 0; }
  html, body {
    width: 1200px;
    height: 716px;
    overflow: hidden;
    background: var(--backdrop);
    font-family: "Open Sans", Arial, sans-serif;
  }
  .stage {
    position: relative;
    width: 1200px;
    height: 716px;
  }
  .card {
    position: absolute;
    top: 204px;
    width: 540px;
    height: 308px;
    background: var(--card);
    overflow: hidden;
    box-shadow: 0 10px 28px rgba(0, 0, 0, 0.45);
  }
  .card--front { left: 50px; }
  .card--back { left: 610px; }

  .emboss-circle {
    position: absolute;
    width: 340px;
    height: 340px;
    border-radius: 50%;
    background: var(--emboss);
    top: 60px;
  }
  .card--front .emboss-circle { left: 380px; }
  .card--back .emboss-circle { left: -180px; }

  .wordmark {
    position: absolute;
    display: flex;
    align-items: center;
    gap: 12px;
  }
  .wordmark__dot {
    width: 38px;
    height: 38px;
    border-radius: 50%;
    background: var(--accent);
    flex: none;
  }
  .wordmark__name {
    color: var(--ink);
    font-weight: 700;
    font-size: 30px;
    letter-spacing: 3px;
    line-height: 1;
  }
  .wordmark__tag {
    color: var(--ink-soft);
    font-size: 8.5px;
    letter-spacing: 1.4px;
    text-transform: uppercase;
    margin-top: 4px;
  }
  .card--front .wordmark { left: 70px; top: 92px; }
  .card--back .wordmark { right: 40px; top: 40px; }
  .card--back .wordmark__name { font-size: 24px; }
  .card--back .wordmark__dot { width: 30px; height: 30px; }

  .contact {
    position: absolute;
    right: 40px;
    top: 118px;
    text-align: right;
    color: var(--ink);
  }
  .contact__name {
    color: var(--accent);
    font-weight: 700;
    font-size: 20px;
    letter-spacing: 1px;
    text-transform: uppercase;
    line-height: 1.1;
  }
  .contact__role {
    font-size: 14px;
    margin-top: 2px;
  }
  .contact__address {
    font-size: 13.5px;
    line-height: 1.35;
    margin-top: 12px;
  }
  .contact__list {
    list-style: none;
    font-size: 13px;
    line-height: 1.5;
    margin-top: 10px;
  }
  .contact__list li {
    display: flex;
    justify-content: flex-end;
    align-items: center;
    gap: 7px;
  }
  .contact__list svg {
    width: 11px;
    height: 11px;
    fill: var(--accent);
    flex: none;
  }
  .accent-bar {
    position: absolute;
    right: 14px;
    top: 140px;
    width: 7px;
    height: 48px;
    background: var(--accent);
  }
</style>
</head>
<body>
<main class="stage">
  <section class="card card--front" aria-label="Card front">
    <div class="emboss-circle"></div>
    <div class="wordmark">
      <span class="wordmark__dot"></span>
      <div>
        <div class="wordmark__name">QUARROW</div>
        <div class="wordmark__tag">Signal Instruments</div>
      </div>
    </div>
  </section>

  <section class="card card--back" aria-label="Card back">
    <div class="emboss-circle"></div>
    <div class="wordmark">
      <span class="wordmark__dot"></span>
      <div>
        <div class="wordmark__name">QUARROW</div>
        <div class="wordmark__tag">Signal Instruments</div>
      </div>
    </div>
    <div class="accent-bar"></div>
    <div class="contact">
      <div class="contact__name">Dana Whitlow</div>
      <div class="contact__role">Managing Director</div>
      <div class="contact__address">Your address, City<br>State, Zip 1234</div>
      <ul class="contact__list">
        <li>123 456 789
          <svg viewBox="0 0 24 24" aria-hidden="true"><path d="M6.6 10.8a15.1 15.1 0 0 0 6.6 6.6l2.2-2.2a1 1 0 0 1 1-.25 11.4 11.4 0 0 0 3.6.57 1 1 0 0 1 1 1V20a1 1 0 0 1-1 1A17 17 0 0 1 3 4a1 1 0 0 1 1-1h3.5a1 1 0 0 1 1 1c0 1.25.2 2.45.57 3.6a1 1 0 0 1-.25 1z"/></svg>
        </li>
        <li>info@yourgmail.com
          <svg viewBox="0 0 24 24" aria-hidden="true"><path d="M2 5h20v14H2z M2 5l10 8 10-8" fill="currentColor"/><path d="M2 5h20v2l-10 7L2 7z"/><rect x="2" y="8" width="20" height="11"/></svg>
        </li>
        <li>www.yourwebsite.com
          <svg viewBox="0 0 24 24" aria-hidden="true"><circle cx="12" cy="12" r="10"/></svg>
        </li>
      </ul>
    </div>
  </section>
</main>
</body>
</html>
```